Property management company looking for modern card design

We at Blue Heron Partners provides property management services for its residential and commercial properties, with expertise in all categories of multifamily, industrial and office projects throughout California.

We need a business card design that is professional and modern designed business card. In our field, clients get hundreds of business cards, we would like our card to stand out.

Please avoid small print.

Target Market(s)

Professionals and high end clients

Industry/Entity Type

Financial Planning

Contact Information for Business Card

Company Name: Blue Heron Partners, Name, email, license #, phone number, website blueheronpartners.com

Font styles to use
Sans Serif

Requirements
Must have
• The card design needs to be adaptable because there is a possibly we will be expanding into different sectors other than real estate. The card design should be focused on financial planning and asset management.
Nice to have
• Modern and simple business card. Eye catching. Non-standard size/shaped cards would be great.
• blueheronpartners.com
Should not have
• Too many bright color or any pictures or shapes of real estate stuff.

```html
<!DOCTYPE html>
<html lang="en">
<head>
<meta charset="utf-8">
<title>Blue Heron Partners – Business Card</title>
<link rel="stylesheet" href="https://fonts.googleapis.com/css2?family=Cabin:wght@400;500;600;700&family=Roboto:wght@500&display=swap">
<style>
  :root {
    --backdrop: #8a4a1c;
    --card: #f1f3f1;
    --brand-red: #a8121c;
    --mark-red: #f0182e;
    --ink: #1f2426;
    --muted: #4d4f52;
  }
  * { margin: 0; padding: 0; box-sizing: border-box; }
  html, body { width: 900px; height: 1200px; overflow: hidden; }
  body {
    background: var(--backdrop);
    font-family: "Cabin", sans-serif;
    color: var(--ink);
    position: relative;
  }
  .card {
    position: absolute;
    background: var(--card);
    box-shadow: 0 2px 10px rgba(0,0,0,.25);
  }
  .card--front { left: 314px; top: 142px; width: 302px; height: 527px; }
  .card--back  { left: 186px; top: 723px; width: 527px; height: 302px; }

  .brand {
    position: absolute;
    left: 0; right: 0;
    display: flex; flex-direction: column; align-items: center;
  }
  .brand__dot {
    width: 56px; height: 56px; border-radius: 50%;
    background: var(--mark-red);
  }
  .brand__name {
    margin-top: 30px;
    font-family: "Cabin", sans-serif;
    font-weight: 600;
    font-size: 20px;
    letter-spacing: 3px;
    color: var(--brand-red);
    white-space: nowrap;
  }
  .card--front .brand { top: 84px; }
  .card--back .brand  { top: 96px; }

  .person {
    position: absolute; right: 33px; top: 258px; text-align: right;
  }
  .person__name { font-size: 31px; font-weight: 600; line-height: 1; }
  .person__title { font-size: 13px; margin-top: 6px; }

  .contact {
    position: absolute; right: 33px; top: 412px; text-align: right;
    font-size: 13px; font-weight: 700; line-height: 22px;
  }
  .website {
    font-family: "Roboto", sans-serif;
    font-weight: 500;
    color: var(--ink);
  }
  .contact .website { font-size: 17px; margin-top: 4px; line-height: 24px; }
  .card--back .website {
    position: absolute; left: 0; right: 0; top: 264px;
    text-align: center; font-size: 18px; color: var(--muted);
  }
</style>
</head>
<body>
  <section class="card card--front">
    <div class="brand">
      <span class="brand__dot"></span>
      <span class="brand__name">Blue Heron Partners</span>
    </div>
    <div class="person">
      <p class="person__name">John Smith</p>
      <p class="person__title">managing director</p>
    </div>
    <div class="contact">
      <p>john.smith@blueheronpartners.com</p>
      <p>555-555-5555</p>
      <p>License Nr:000001</p>
      <p class="website">blueheronpartners.com</p>
    </div>
  </section>

  <section class="card card--back">
    <div class="brand">
      <span class="brand__dot"></span>
      <span class="brand__name">Blue Heron Partners</span>
    </div>
    <p class="website">blueheronpartners.com</p>
  </section>
</body>
</html>
```